Food and Beverage Business Cards

We need business cards with logo designs for a consultant in the food and beverage industry. We specialize in helping restaurants fix operational and management problems.
Specific areas of expertise include:
-Steps of service
-Staff management tools
-Standard operating procedures
-Profit and loss management
-Inventory
-Point of sales
-Bar Menu
-Mystery shopper service
-Handling and managing suppliers

Target Market(s)

Restaurant and bar owners and managers

Industry/Entity Type

Business

Contact Information for Business Card

Mathieu Girardot
Q&T Consulting
phone: 15027390614
mathqt@sampleinbox.com

Font styles to use
Other font styles liked:
• Check out the screen shot font idea

Colors

Designer to choose colors to be used in the design.

Requirements
Must have
• Must include QR code (See attachment)
• Logo should reflect our specific focus on the drinks side of the industry.
• Areas of Expertise:
• -Service Steps
• -Staff management tools
• -S.O.P
• -P&L Management
• -Inventory
• -P.O.S
• -Bar Menu
• -Mystery Shopper Service
• -Handling and Managing Suppliers

```html
<!DOCTYPE html>
<html lang="en">
<head>
<meta charset="utf-8">
<title>Q&amp;T Consulting Business Card</title>
<link rel="stylesheet" href="https://fonts.googleapis.com/css2?family=Roboto:wght@400;500;700&display=swap">
<style>
  :root {
    --backdrop: #2a2a2a;
    --card-dark: #1c1c1c;
    --card-light: #f6f6f4;
    --ink-light: #ffffff;
    --ink-dark: #161616;
    --ink-muted: #5a5a5a;
    --divider: #9a9a9a;
    --badge-grey: #6e6e6e;
    --badge-light: #bdbdbd;
    --badge-green: #9fd9a8;
  }
  * { box-sizing: border-box; margin: 0; padding: 0; }
  html, body { width: 1200px; height: 900px; overflow: hidden; }
  body {
    background: var(--backdrop);
    font-family: "Roboto", Arial, sans-serif;
    display: flex;
    flex-direction: column;
    align-items: center;
    justify-content: center;
    gap: 40px;
  }
  .card {
    width: 660px;
    height: 377px;
    position: relative;
    box-shadow: 0 10px 30px rgba(0,0,0,0.45);
  }
  .card--front { background: var(--card-dark); color: var(--ink-light); text-align: center; }
  .card--back { background: var(--card-light); color: var(--ink-dark); }

  .badges { position: absolute; top: 26px; right: 30px; display: flex; gap: 8px; }
  .badge { width: 44px; height: 44px; border-radius: 50%; }
  .badge--grey { background: var(--badge-grey); }
  .badge--light { background: var(--badge-light); }
  .badge--green { background: var(--badge-green); }

  .brand { padding-top: 52px; }
  .brand__name { font-size: 64px; font-weight: 700; letter-spacing: 2px; line-height: 1; }
  .brand__place { font-size: 20px; font-weight: 700; letter-spacing: 6px; margin-top: 6px; text-transform: lowercase; }

  .expertise { margin-top: 26px; }
  .expertise__title { font-size: 20px; font-weight: 700; margin-bottom: 8px; }
  .expertise__list { list-style: none; font-size: 16px; line-height: 1.35; }

  .identity {
    position: absolute; top: 160px; right: 345px; text-align: right;
  }
  .identity__name { font-size: 24px; font-weight: 700; text-transform: uppercase; letter-spacing: 0.3px; }
  .identity__role { font-size: 17px; font-weight: 400; color: var(--ink-muted); text-transform: uppercase; letter-spacing: 1px; margin-top: 2px; }

  .divider {
    position: absolute; left: 332px; top: 150px; width: 1.5px; height: 90px;
    background: linear-gradient(to bottom, transparent, var(--divider), transparent);
  }

  .contact { position: absolute; left: 360px; top: 170px; list-style: none; font-size: 18px; color: var(--ink-muted); }
  .contact__item { display: flex; align-items: center; gap: 12px; margin-bottom: 10px; }
  .contact__icon { width: 16px; height: 16px; fill: var(--ink-dark); flex-shrink: 0; }
</style>
</head>
<body>
  <section class="card card--front">
    <div class="badges">
      <span class="badge badge--grey"></span>
      <span class="badge badge--light"></span>
      <span class="badge badge--green"></span>
    </div>
    <div class="brand">
      <div class="brand__name">Q&amp;T</div>
      <div class="brand__place">Harbor</div>
    </div>
    <div class="expertise">
      <h2 class="expertise__title">Areas of Expertise</h2>
      <ul class="expertise__list">
        <li>Service Steps | Staff management tools | S.O.P | P&amp;L Management</li>
        <li>Inventory | P.O.S | Bar Menu | Mystery Shopper Service</li>
        <li>Handling and Managing Suppliers</li>
      </ul>
    </div>
  </section>

  <section class="card card--back">
    <div class="identity">
      <h1 class="identity__name">Mathieu Girardot</h1>
      <p class="identity__role">Q&amp;T Consulting</p>
    </div>
    <div class="divider"></div>
    <ul class="contact">
      <li class="contact__item">
        <svg class="contact__icon" viewBox="0 0 24 24" aria-hidden="true"><path d="M6.6 10.8a15.1 15.1 0 0 0 6.6 6.6l2.2-2.2a1 1 0 0 1 1-.25 11.4 11.4 0 0 0 3.6.57 1 1 0 0 1 1 1V20a1 1 0 0 1-1 1A17 17 0 0 1 3 4a1 1 0 0 1 1-1h3.5a1 1 0 0 1 1 1c0 1.25.2 2.45.57 3.57a1 1 0 0 1-.25 1z"/></svg>
        <span>15027390614</span>
      </li>
      <li class="contact__item">
        <svg class="contact__icon" viewBox="0 0 24 24" aria-hidden="true"><path d="M2 5h20v14H2z M2 5l10 7 10-7" fill-rule="evenodd"/><path d="M3 6.2l9 6.3 9-6.3V18H3z" fill="#f6f6f4" opacity="0"/></svg>
        <span>mathqt@sampleinbox.com</span>
      </li>
    </ul>
  </section>
</body>
</html>
```